Water ATM Card

Need a design for water ATM cards. Size of card is 3.375 x 2.125 inch
On the Front include the Cedar hollow Logo.
Bottom right corner should have Price $100
On the Back
This card is to be used to access water refills at any Cedar Hollow Water Vending Machines.
Please contact (869) 418 2930 or (869) 534 1276 or email clearflowbox@mailvista.example for any assistance or recharging of card.

```html
<!DOCTYPE html>
<html lang="en">
<head>
<meta charset="utf-8">
<title>Cedar Hollow Water Card</title>
<link rel="stylesheet" href="https://fonts.googleapis.com/css2?family=Montserrat:wght@400;500;700&display=swap">
<style>
  :root {
    --backdrop: #9b9b9b;
    --card-white: #ffffff;
    --brand-blue: #2a5aa8;
    --price-green: #2e9e45;
    --ink: #1d1d1f;
    --back-top: #2f82c4;
    --back-mid: #3d569a;
    --back-bottom: #2b3a86;
    --on-dark: #ffffff;
  }
  * { margin: 0; padding: 0; box-sizing: border-box; }
  html, body {
    width: 1093px; height: 1200px; overflow: hidden;
    background: var(--backdrop);
    font-family: "Montserrat", sans-serif;
  }
  .card {
    position: absolute;
    left: 264px;
    width: 581px;
    height: 363px;
    border-radius: 18px;
    overflow: hidden;
  }
  .card--front { top: 225px; background: var(--card-white); }
  .card--back {
    top: 616px; height: 366px;
    background: linear-gradient(160deg, var(--back-top) 0%, var(--back-mid) 50%, var(--back-bottom) 100%);
  }

  .brand-name {
    position: absolute; left: 33px; top: 48px;
    font-weight: 700; font-size: 21px; letter-spacing: 0.2px;
    color: var(--brand-blue); text-transform: uppercase;
  }
  .price {
    position: absolute; right: 31px; bottom: 30px;
    font-weight: 700; font-size: 30px; color: var(--price-green);
  }
  .holder { position: absolute; left: 33px; top: 116px; }
  .holder-name {
    font-weight: 700; font-size: 20px; color: var(--brand-blue); text-transform: uppercase;
  }
  .holder-role { font-size: 13px; color: var(--ink); margin-top: 4px; font-weight: 400; }
  .address {
    position: absolute; left: 33px; top: 180px;
    font-size: 13px; line-height: 16.5px; color: var(--ink);
  }
  .contacts { position: absolute; left: 33px; top: 234px; list-style: none; }
  .contact {
    display: flex; align-items: center; gap: 6px;
    font-size: 13px; color: var(--ink); height: 22px;
  }
  .contact svg { width: 12px; height: 13px; fill: var(--brand-blue); flex: none; }

  .back-name {
    position: absolute; left: 0; right: 0; top: 150px;
    text-align: center; font-weight: 700; font-size: 35px;
    color: var(--on-dark); text-transform: uppercase; letter-spacing: 0.5px;
  }
  .back-note {
    position: absolute; left: 50px; right: 50px; top: 248px;
    text-align: center; font-size: 13px; line-height: 19px; color: var(--on-dark);
  }
</style>
</head>
<body>
  <section class="card card--front" aria-label="Card front">
    <div class="brand-name">Cedar Hollow</div>
    <div class="price">Price $100</div>
    <div class="holder">
      <div class="holder-name">Daniel Reyes</div>
      <div class="holder-role">OWER</div>
    </div>
    <p class="address">845 Ridgeline Avenue, Ste<br>210 Knoxville, TN37902</p>
    <ul class="contacts">
      <li class="contact">
        <svg viewBox="0 0 24 24"><path d="M6.6 10.8a15 15 0 0 0 6.6 6.6l2.2-2.2c.3-.3.7-.4 1-.2 1.1.4 2.3.6 3.6.6.6 0 1 .4 1 1V20c0 .6-.4 1-1 1A17 17 0 0 1 3 4c0-.6.4-1 1-1h3.5c.6 0 1 .4 1 1 0 1.3.2 2.5.6 3.6.1.3 0 .7-.2 1z"/></svg>
        (869) 418 2930
      </li>
      <li class="contact">
        <svg viewBox="0 0 24 24"><path d="M7 1h10a2 2 0 0 1 2 2v18a2 2 0 0 1-2 2H7a2 2 0 0 1-2-2V3a2 2 0 0 1 2-2zm0 3v14h10V4zm5 15.5a1.2 1.2 0 1 0 0 2.4 1.2 1.2 0 0 0 0-2.4z"/></svg>
        (869) 534 1276
      </li>
      <li class="contact">
        <svg viewBox="0 0 24 24"><path d="M2 5h20v2.2l-10 6-10-6zm0 4.5 10 6 10-6V19H2z"/></svg>
        clearflowbox@mailvista.example
      </li>
      <li class="contact">
        <svg viewBox="0 0 24 24"><circle cx="12" cy="12" r="10"/><path d="M8 6c2 1 1 3 3 3s1 3-1 3-3 2-2 5M15 5c-1 2 1 3 3 3M14 14c2 0 3 2 2 5" stroke="#fff" stroke-width="1.6" fill="none"/></svg>
        www.cedarhollowwater.example
      </li>
    </ul>
  </section>

  <section class="card card--back" aria-label="Card back">
    <div class="back-name">Cedar Hollow</div>
    <p class="back-note">This card is to be used to access water refills at any Cedar Hollow Water Vending Machines. Please contact (869) 418 2930 or (869) 534 1276 or email clearflowbox@mailvista.example for any assistance or recharging of card.</p>
  </section>
</body>
</html>
```